Breakfast Cafe - The Sunny Nook

It is for my breakfast and lunch cafe with a hawaiian / beach theme. I am open 7 days a week from 7am to 2pm. We serve traditional American food such as omelettes, pancakes, burgers and sandwiches. I'll upload my old card and my new logo to be used. We have a lot of day to day regulars who eat there during the week, our t-shirts actually say 'Locals Only' on them. Hope this helps. Thanks.

Target Market(s)

anyone who has an appetite!

Industry/Entity Type

American Restaurant

Contact Information for Business Card

4815C Marlow Grove Avenue
Long Beach, California
(555) 731-2294

Requirements
Must have
• Address and phone number easily readable.
Nice to have
• beach or tropical theme

```html
<!DOCTYPE html>
<html lang="en">
<head>
<meta charset="utf-8">
<title>The Sunny Nook – Business Card</title>
<link href="https://fonts.googleapis.com/css2?family=Bebas+Neue&family=Dancing+Script:wght@600&display=swap" rel="stylesheet">
<style>
  :root {
    --backdrop: #2a2a2a;
    --wood-dark: #8a4508;
    --wood-mid: #b0600f;
    --wood-light: #c4741c;
    --paper: #f3f3f1;
    --ink: #2e2e2e;
    --sun-orange: #f2a33a;
    --accent-orange: #c0650f;
    --ocean-blue: #3aaed2;
  }
  * { margin: 0; padding: 0; box-sizing: border-box; }
  html, body {
    width: 1200px;
    height: 960px;
    overflow: hidden;
    background: var(--backdrop);
  }
  .card {
    position: absolute;
    left: 429px;
    top: 181px;
    width: 344px;
    height: 600px;
    border-radius: 16px;
    background: repeating-linear-gradient(90deg,
      var(--wood-mid) 0px, var(--wood-light) 2px, var(--wood-dark) 4px, var(--wood-mid) 6px);
  }
  .card-face {
    position: absolute;
    left: 13px;
    top: 14px;
    width: 316px;
    height: 572px;
    border-radius: 22px;
    background: var(--paper);
    font-family: "Bebas Neue", sans-serif;
    color: var(--ink);
    text-align: center;
  }
  .line {
    position: absolute;
    left: 0;
    width: 100%;
    line-height: 1;
    white-space: nowrap;
  }
  .brand-mark {
    position: absolute;
    left: 68px;
    top: 20px;
    width: 170px;
    height: 170px;
    border-radius: 50%;
    background: var(--sun-orange);
  }
  .brand-name { top: 167px; font-size: 40px; color: var(--ocean-blue); }
  .brand-place { top: 210px; font-size: 11px; letter-spacing: 3px; color: var(--accent-orange); }
  .address { font-size: 25px; }
  .address-street { top: 248px; }
  .address-city { top: 273px; }
  .phone { top: 302px; font-size: 30px; }
  .divider-dot {
    position: absolute;
    left: 143px;
    top: 350px;
    width: 30px;
    height: 30px;
    border-radius: 50%;
    background: var(--wood-mid);
  }
  .cafe-type { top: 399px; font-size: 25px; }
  .hours { top: 429px; font-size: 19px; }
  .cuisine { top: 454px; font-size: 15px; }
  .rule {
    position: absolute;
    left: 124px;
    top: 488px;
    width: 56px;
    height: 2px;
    background: var(--accent-orange);
  }
  .tagline {
    top: 503px;
    font-family: "Dancing Script", cursive;
    font-weight: 600;
    font-size: 38px;
  }
</style>
</head>
<body>
  <div class="card">
    <div class="card-face">
      <div class="brand-mark"></div>
      <div class="line brand-name">The Sunny Nook</div>
      <div class="line brand-place">Long Beach, CA</div>
      <div class="line address address-street">4815C Marlow Grove Avenue</div>
      <div class="line address address-city">Long Beach, California</div>
      <div class="line phone">P.(555) 731-2294</div>
      <div class="divider-dot"></div>
      <div class="line cafe-type">Breakfast &amp; Lunch Cafe</div>
      <div class="line hours">Open 7 days a week from 7am to 2pm.</div>
      <div class="line cuisine">Serving traditional American food</div>
      <div class="rule"></div>
      <div class="line tagline">Locals Only</div>
    </div>
  </div>
</body>
</html>
```